Tollen Ridge Canvas Camps

I am Moving from nest QiV and Qelt to host my own website to create direct bookings. I haves booking platform, I just need a website to embed it into. I want a catchy website to attract potential guests to book at my accommodation located near morvane national park in Alberta, Canada.

Here is my nest QiV links:
https://www.nestqiv.ca/rooms/2048613927465105319?viralityEntryPoint=1&s=76

https://www.nestqiv.ca/rooms/2093547718260493127?viralityEntryPoint=1&s=76

https://www.nestqiv.ca/rooms/2184736590218374662?viralityEntryPoint=1&s=76

https://www.nestqiv.ca/rooms/2065128834710952483?viralityEntryPoint=1&s=76

https://www.nestqiv.ca/rooms/2317465098321857704?viralityEntryPoint=1&s=76

```html
<!DOCTYPE html>
<html lang="en">
<head>
<meta charset="utf-8">
<title>Tollen Ridge Canvas Camps</title>
<link href="https://fonts.googleapis.com/css2?family=Poppins:ital,wght@0,400;0,500;0,600;0,700;1,400&display=swap" rel="stylesheet">
<style>
:root{
  --accent:#e3174a;
  --ink:#2b2b2b;
  --muted:#555;
  --paper:#ffffff;
  --mist:#f1f1f1;
  --night:#120f1e;
  --aurora-green:#2f6b4a;
  --aurora-violet:#4b2a6e;
  --line:#d9d9d9;
}
*{margin:0;padding:0;box-sizing:border-box}
html,body{width:1200px;height:4800px;overflow:hidden}
body{font-family:'Poppins',sans-serif;color:var(--ink);background:var(--paper);position:relative}
section,header,footer{position:absolute;left:0;width:1200px}
.abs{position:absolute}
.btn{position:absolute;display:flex;align-items:center;justify-content:center;background:var(--accent);color:#fff;font-weight:600;border-radius:30px;font-size:16px}
.btn-outline{position:absolute;display:flex;align-items:center;justify-content:center;border:2px solid var(--accent);color:var(--accent);font-weight:600;border-radius:30px;background:transparent}
.photo{position:absolute;overflow:hidden}

/* hero */
.hero{top:0;height:652px;background:
  radial-gradient(ellipse at 75% 10%,#5b2f8a 0%,transparent 45%),
  radial-gradient(ellipse at 30% 25%,#2c5e44 0%,transparent 45%),
  radial-gradient(ellipse at 85% 80%,#7a4a22 0%,transparent 35%),
  linear-gradient(180deg,#1b1630 0%,#0d0d12 70%,#07070a 100%)}
.brand{position:absolute;left:75px;top:60px;display:flex;align-items:center;gap:12px;color:#fff;font-weight:600;font-size:18px;line-height:1.2;width:240px}
.brand-dot{width:44px;height:44px;border-radius:50%;background:#fff;flex:none}
.nav{position:absolute;left:397px;top:80px;display:flex;gap:31px;color:#fff;font-weight:600;font-size:15px}
.nav .current{border-bottom:2px solid #fff;padding-bottom:3px}
.hero-title{position:absolute;top:248px;width:100%;text-align:center;color:#fff;font-weight:700;font-size:52px;line-height:58px}
.hero-sub{position:absolute;top:370px;width:100%;text-align:center;color:#fff;font-size:22px;line-height:31px}

/* about */
.about{top:652px;height:540px}
.about h2{position:absolute;left:615px;top:76px;font-size:46px;line-height:50px;font-weight:700}
.about p{position:absolute;left:615px;top:198px;width:520px;font-size:13px;line-height:26.5px;color:var(--ink)}

/* featured */
.featured{top:1192px;height:550px;background:var(--mist)}
.section-title{font-size:44px;font-weight:700;line-height:1.2}
.card{position:absolute;top:149px;width:242px}
.card .photo{position:relative;height:173px;border-radius:16px 16px 6px 6px}
.card h3{font-size:15px;font-weight:700;line-height:24px;margin-top:18px}
.meta{display:flex;gap:12px;font-size:12px;margin-top:12px;color:var(--ink)}
.card .btn-outline{position:relative;width:168px;height:40px;font-size:13px;margin-top:18px}

/* experience */
.experience{top:1742px;height:695px}
.tile{position:absolute;width:328px;height:205px;border-radius:14px;display:flex;align-items:flex-end;justify-content:center;padding-bottom:32px;color:#fff;font-weight:600;font-size:19px}

/* band */
.band{top:2437px;height:302px;background:linear-gradient(180deg,#1e2040 0%,#2f2a55 40%,#1a2a30 100%);display:flex;align-items:center;justify-content:center;text-align:center;color:#fff;font-size:44px;font-weight:700;line-height:52px}

/* amenities */
.amenities{top:2739px;height:410px}
.amenity{position:absolute;top:145px;height:182px;border-left:3px solid var(--accent);padding:52px 0 0 20px;width:260px}
.amenity h3{color:var(--accent);font-size:20px;font-weight:600;line-height:26px;margin-bottom:6px}
.amenity li{list-style:none;font-size:14px;line-height:31.5px;display:flex;align-items:center;gap:12px;color:var(--ink)}

/* reviews */
.reviews{top:3149px;height:387px;background:var(--mist)}
.reviews h2{position:absolute;left:75px;top:84px;font-size:44px;line-height:46px;font-weight:700}
.quote{position:absolute;left:525px;top:104px;width:610px;font-style:italic;font-size:26px;line-height:43px}
.quote-name{position:absolute;left:525px;top:244px;color:var(--accent);font-size:20px;font-weight:600}

/* faq */
.faq{top:3536px;height:572px}
.faq-item{position:absolute;left:75px;width:506px;border-bottom:1px solid var(--line);padding-bottom:14px;display:flex;justify-content:space-between;align-items:center;font-size:16px;font-weight:500}
.faq-open{position:absolute;left:75px;top:152px;width:506px}
.faq-open h3{color:var(--accent);font-size:17px;font-weight:600}
.faq-open p{font-size:12.5px;line-height:24px;margin-top:10px}

/* cta */
.cta{top:4108px;height:341px;background:linear-gradient(180deg,#1c2226 0%,#2d3a34 55%,#14191a 100%)}
.cta h2{position:absolute;top:88px;width:100%;text-align:center;color:#fff;font-size:46px;line-height:52px;font-weight:700}

/* footer */
.site-footer{top:4449px;height:351px}
.footer-brand{position:absolute;left:84px;top:72px;width:224px;text-align:center;color:var(--ink);font-weight:600;font-size:20px;line-height:26px}
.footer-col{position:absolute;top:67px}
.footer-col h4{font-size:17px;font-weight:600;margin-bottom:6px}
.footer-col li{list-style:none;font-size:13.5px;line-height:29px}
.socials{position:absolute;left:108px;top:276px;display:flex;gap:19px}
.socials span{width:20px;height:20px;border-radius:50%;background:var(--ink)}
</style>
</head>
<body>

<header class="hero">
  <div class="photo" style="inset:0" role="img" aria-label="Night sky with northern lights above pine forest and a glowing glamping dome"></div>
  <div class="brand"><span class="brand-dot"></span>Tollen Ridge Canvas Camps</div>
  <nav class="nav">
    <span class="current">Home</span><span>Stays</span><span>Experience</span><span>Gallery</span><span>Location</span><span>About</span>
  </nav>
  <a class="btn" style="left:954px;top:65px;width:171px;height:56px">Book Your Stay</a>
  <h1 class="hero-title">Sleep Under the Stars.<br>Wake in the Rockies.</h1>
  <p class="hero-sub">Private heated domes &amp; safari tents surrounded by nature<br>without giving up modern comfort.</p>
  <a class="btn" style="left:495px;top:456px;width:210px;height:56px">Check Availability</a>
</header>

<section class="about">
  <div class="photo" style="left:75px;top:75px;width:422px;height:295px;border-radius:36px;background:linear-gradient(160deg,#3a2a6a,#2d6a4a 50%,#0c0c10)" role="img" aria-label="Aurora over dark pine trees at the camp"></div>
  <div class="photo" style="left:250px;top:253px;width:338px;height:210px;border-radius:36px;border:4px solid #fff;background:linear-gradient(160deg,#e9e3d8,#b9ab93 60%,#7a5a45)" role="img" aria-label="Interior of a furnished glamping dome with chairs and a bed"></div>
  <h2>About Tollen Ridge<br>Canvas Camps</h2>
  <p>Nemo enim ipsam voluptatem quia voluptas sit aspernatur aut odit aut fugit, sed quia consequuntur magni dolores eos qui ratione voluptatem sequi nesciunt. Neque porro quisquam est, qui dolorem ipsum quia dolor sit amet, consectetur, adipisci velit, sed quia non numquam eius modi tempora incidunt ut labore et dolore magnam aliquam quaerat voluptatem. sunt in culpa qui officia deserunt mollit anim id est laborum.</p>
  <a class="btn" style="left:615px;top:397px;width:144px;height:50px;font-size:15px">Read More</a>
</section>

<section class="featured">
  <h2 class="section-title abs" style="left:73px;top:64px">Featured Listing</h2>
  <svg class="abs" style="left:1065px;top:83px" width="80" height="30" viewBox="0 0 80 30" fill="none" stroke-width="2.5" stroke-linecap="round" stroke-linejoin="round">
    <path d="M15 5 L5 15 L15 25" stroke="#222"/>
    <path d="M53 5 L63 15 L53 25" stroke="var(--accent)"/>
  </svg>
  <div class="card" style="left:75px">
    <div class="photo" style="background:linear-gradient(180deg,#6a7a86,#c9d2d6 55%,#5d6b4a)" role="img" aria-label="Clear dome under a rainbow and storm clouds"></div>
    <h3>Dome in Yellowhead<br>County, Canada</h3>
    <div class="meta"><span>4Guest</span><span>1 Bedroom</span><span>1 Bath</span></div>
    <a class="btn-outline">Check Availability</a>
  </div>
  <div class="card" style="left:345px">
    <div class="photo" style="background:linear-gradient(180deg,#e6e0d4,#b8a891 60%,#6d4c3a)" role="img" aria-label="Dome interior with chairs and mountain window"></div>
    <h3>Dome in Yellowhead<br>County, Canada</h3>
    <div class="meta"><span>4Guest</span><span>1 Bedroom</span><span>1 Bath</span></div>
    <a class="btn-outline">Check Availability</a>
  </div>
  <div class="card" style="left:615px">
    <div class="photo" style="background:linear-gradient(180deg,#9fb0b8,#56664a 50%,#8a7a60)" role="img" aria-label="White dome in a forest clearing"></div>
    <h3>Dome in Yellowhead<br>County, Canada</h3>
    <div class="meta"><span>4Guest</span><span>1 Bedroom</span><span>1 Bath</span></div>
    <a class="btn-outline">Check Availability</a>
  </div>
  <div class="card" style="left:885px">
    <div class="photo" style="background:linear-gradient(160deg,#3a2c24,#a49478 55%,#6c7a5a)" role="img" aria-label="Cosy deck with chairs overlooking the mountains"></div>
    <h3>Dome in Yellowhead<br>County, Canada</h3>
    <div class="meta"><span>4Guest</span><span>1 Bedroom</span><span>1 Bath</span></div>
    <a class="btn-outline">Check Availability</a>
  </div>
  <a class="btn" style="left:499px;top:526px;width:202px;height:46px;font-size:15px">View All Listing</a>
</section>

<section class="experience">
  <h2 class="section-title abs" style="width:100%;text-align:center;top:90px">More Than a Stay — An Experience</h2>
  <div class="tile" style="left:75px;top:181px;background:linear-gradient(160deg,#1d2a36,#3a2c24 60%,#b0602a)" role="img" aria-label="Campfire beside a tent at night">Campfires &amp; S'mores</div>
  <div class="tile" style="left:436px;top:181px;background:linear-gradient(180deg,#0e1630,#2a3a5a 60%,#3a2a20)" role="img" aria-label="Starry sky over the camp">Stargazing</div>
  <div class="tile" style="left:797px;top:181px;background:linear-gradient(160deg,#9a8a78,#6e6456 60%,#4a4236)" role="img" aria-label="Wildlife in the forest">Wildlife Sightings</div>
  <div class="tile" style="left:75px;top:414px;background:linear-gradient(160deg,#4a5a5e,#2e3a34 60%,#5a6a6a)" role="img" aria-label="Hikers crossing a mountain trail">Hiking Adventures</div>
  <div class="tile" style="left:436px;top:414px;background:linear-gradient(180deg,#0f1a30,#2a3e5a 60%,#8a9aaa)" role="img" aria-label="Snowy pine trees on a winter night">Winter Snow Magic</div>
  <div class="tile" style="left:797px;top:414px;background:linear-gradient(180deg,#3a2a60,#2a5a4a 55%,#0c0c12)" role="img" aria-label="Glowing dome under aurora">Instagram-worthy Views</div>
</section>

<section class="band" role="img" aria-label="Aurora over a lake and forest at night">
  <h2 style="font-size:44px;line-height:52px">Close to Morvane<br>Away From the Crowds</h2>
</section>

<section class="amenities">
  <h2 class="section-title abs" style="width:100%;text-align:center;top:44px">Amenities</h2>
  <svg width="0" height="0" style="position:absolute"><defs><symbol id="tick" viewBox="0 0 14 14"><path d="M2 7.5 L5.5 11 L12 3.5" fill="none" stroke="#2b2b2b" stroke-width="2" stroke-linecap="round" stroke-linejoin="round"/></symbol></defs></svg>
  <div class="amenity" style="left:75px">
    <h3>Comfort</h3>
    <ul><li><svg width="13" height="13"><use href="#tick"/></svg>Heated tents</li><li><svg width="13" height="13"><use href="#tick"/></svg>Premium mattresses</li><li><svg width="13" height="13"><use href="#tick"/></svg>Cozy blankets</li></ul>
  </div>
  <div class="amenity" style="left:343px">
    <h3>Convenience</h3>
    <ul><li><svg width="13" height="13"><use href="#tick"/></svg>Parking</li><li><svg width="13" height="13"><use href="#tick"/></svg>Self check-in</li><li><svg width="13" height="13"><use href="#tick"/></svg>Charging outlets</li></ul>
  </div>
  <div class="amenity" style="left:615px">
    <h3>Outdoor</h3>
    <ul><li><svg width="13" height="13"><use href="#tick"/></svg>Firepit</li><li><svg width="13" height="13"><use href="#tick"/></svg>Seating area</li><li><svg width="13" height="13"><use href="#tick"/></svg>Mountain views</li></ul>
  </div>
  <div class="amenity" style="left:883px;width:290px">
    <h3>Extras</h3>
    <ul><li><svg width="13" height="13"><use href="#tick"/></svg>Coffee / tea</li><li><svg width="13" height="13"><use href="#tick"/></svg>Local guidebook</li><li><svg width="13" height="13"><use href="#tick"/></svg>Adventure recommendations</li></ul>
  </div>
</section>

<section class="reviews">
  <h2>Guests<br>Don’t Forget<br>This Stay</h2>
  <a class="btn-outline" style="left:75px;top:257px;width:205px;height:51px;font-size:15px">View All Reviews</a>
  <p class="quote">“We came for one night and wished we stayed a week. Watching the stars from bed was unreal.”</p>
  <p class="quote-name">Name Heading</p>
</section>

<section class="faq">
  <h2 class="section-title abs" style="width:100%;text-align:center;top:64px">FAQ’s</h2>
  <div class="faq-open">
    <div style="display:flex;justify-content:space-between;align-items:center"><h3>Is it warm at night?</h3><svg width="14" height="4"><rect width="14" height="3" fill="var(--accent)"/></svg></div>
    <p>Nemo enim ipsam voluptatem quia voluptas sit aspernatur aut odit aut fugit, sed quia consequuntur magni dolores eos qui ratione.</p>
  </div>
  <div class="faq-item" style="top:258px">Are bathrooms private?<svg width="14" height="14"><path d="M7 1v12M1 7h12" stroke="#2b2b2b" stroke-width="2.5"/></svg></div>
  <div class="faq-item" style="top:312px">Wildlife safety?<svg width="14" height="14"><path d="M7 1v12M1 7h12" stroke="#2b2b2b" stroke-width="2.5"/></svg></div>
  <div class="faq-item" style="top:366px">Winter stays comfortable?<svg width="14" height="14"><path d="M7 1v12M1 7h12" stroke="#2b2b2b" stroke-width="2.5"/></svg></div>
  <div class="faq-item" style="top:420px">Cancellation policy?<svg width="14" height="14"><path d="M7 1v12M1 7h12" stroke="#2b2b2b" stroke-width="2.5"/></svg></div>
  <div class="faq-item" style="top:474px;border-bottom:none">What should we bring?<svg width="14" height="14"><path d="M7 1v12M1 7h12" stroke="#2b2b2b" stroke-width="2.5"/></svg></div>
  <div class="photo" style="left:615px;top:153px;width:512px;height:339px;border-radius:40px;background:linear-gradient(160deg,#3a2a20,#8a6a4a 50%,#c9b49a)" role="img" aria-label="Couple planning a trip together on a laptop"></div>
</section>

<section class="cta">
  <div class="photo" style="inset:0" role="img" aria-label="Glamping dome in a misty pine forest at dusk"></div>
  <h2>Your Unforgettable Rockies<br>Escape Starts Here</h2>
  <a class="btn" style="left:496px;top:205px;width:208px;height:56px">Book Your Stay</a>
</section>

<footer class="site-footer">
  <div class="footer-brand">Tollen Ridge<br>Canvas Camps</div>
  <p class="abs" style="left:84px;top:232px;width:224px;text-align:center;font-size:11.5px;line-height:20px">Copyright © 2026 Company Name<br>All rights reserved.</p>
  <div class="socials"><span></span><span></span><span></span><span></span><span></span></div>
  <div class="footer-col" style="left:371px"><h4>Quick Links</h4><ul><li>Home</li><li>Stays</li><li>Experience</li><li>Gallery</li><li>Location</li><li>About</li><li>Contact Us</li></ul></div>
  <div class="footer-col" style="left:617px"><h4>Experience</h4><ul><li>Campfires</li><li>Stargazing</li><li>Hiking</li><li>Wildlife</li><li>Winter stays</li><li>Romantic escapes</li></ul></div>
  <div class="footer-col" style="left:885px"><h4>About</h4><ul><li>Your story</li><li>Why you started</li><li>Sustainability angle</li><li>Guest philosophy</li></ul></div>
</footer>

</body>
</html>
```